K7 Services business card design contest. Use logo and create a professional layout.

See attached sample. Please sharpen all text and images, don't want any pix-elated content. We are looking for a clean look that quickly provides the information need. Please include our information provided on the sample card. Please feel free to offer any design changes. Please only user the colors provided: #2D3539 & #FFA500. Do not prefer any images other than the K7 Logo

Target Market(s)

Construction, Architects, General Contractors, residential

Industry/Entity Type

Business

Contact Information for Business Card

Company logo, Name, email, fax & phone

Font styles to use
Other font styles liked:
• Josefin Slab

Requirements
Must have
• Name
• Phone & Fax #'s
• address
• Logo
• Website url: www.kq7services.example
Nice to have
• Font Colors #2D3539 & #FFA400
• We prefer a white background.

```html
<!DOCTYPE html>
<html lang="en">
<head>
<meta charset="utf-8">
<title>K7 Services Business Card</title>
<link rel="stylesheet" href="https://fonts.googleapis.com/css2?family=Montserrat:wght@400;500&display=swap">
<style>
  :root {
    --charcoal: #2D3539;
    --orange: #FFA500;
    --white: #FFFFFF;
    --ink: #3a4247;
    --backdrop: #e4e4e4;
  }
  * { box-sizing: border-box; margin: 0; padding: 0; }
  html, body {
    width: 1200px; height: 852px; overflow: hidden;
    background: var(--backdrop);
    font-family: "Montserrat", Arial, sans-serif;
  }
  .sheet {
    width: 1200px; height: 852px;
    display: flex; align-items: center; justify-content: center; gap: 40px;
  }
  .card {
    position: relative; width: 540px; height: 309px;
    border-radius: 14px; overflow: hidden;
    box-shadow: 0 6px 18px rgba(0,0,0,0.18);
  }
  /* Front */
  .card--front {
    background: var(--charcoal);
    display: flex; align-items: center; justify-content: center;
  }
  .brand { display: flex; align-items: center; gap: 18px; color: var(--white); }
  .brand__dot {
    width: 50px; height: 50px; border-radius: 50%;
    border: 3px solid var(--white); flex: none;
  }
  .brand__name { font-weight: 400; font-size: 36px; line-height: 1.1; }
  .brand__tagline { font-weight: 400; font-size: 16px; margin-top: 6px; }
  /* Back */
  .card--back { background: var(--white); }
  .card__shape { position: absolute; inset: 0; }
  .card__brand {
    position: absolute; left: 0; top: 0; width: 240px; height: 100%;
    display: flex; align-items: center; justify-content: center;
  }
  .card__brand .brand { flex-direction: column; gap: 12px; text-align: center; }
  .card__brand .brand__dot { width: 42px; height: 42px; }
  .card__brand .brand__name { font-size: 28px; }
  .card__brand .brand__tagline { font-size: 12.5px; }
  .details {
    position: absolute; left: 282px; top: 34px; right: 20px; bottom: 24px;
    color: var(--ink);
    display: flex; flex-direction: column;
  }
  .details__name { color: var(--orange); font-size: 18px; font-weight: 400; }
  .details__title { font-size: 12px; margin-top: 4px; }
  .details__address { font-size: 11px; line-height: 1.5; margin-top: auto; }
  .contact { list-style: none; margin-top: 8px; font-size: 11.5px; }
  .contact li { display: flex; align-items: center; gap: 8px; line-height: 1.65; }
  .contact svg { width: 12px; height: 12px; fill: var(--orange); flex: none; }
  .services { margin-top: 16px; font-size: 12.5px; letter-spacing: 0.5px; }
  .services__sep { color: var(--orange); padding: 0 3px; }
</style>
</head>
<body>
<main class="sheet">
  <section class="card card--front" aria-label="Card front">
    <div class="brand">
      <span class="brand__dot"></span>
      <div>
        <div class="brand__name">K7 Services</div>
        <div class="brand__tagline">Clear Views From Above</div>
      </div>
    </div>
  </section>

  <section class="card card--back" aria-label="Card back">
    <svg class="card__shape" viewBox="0 0 540 309" preserveAspectRatio="none" aria-hidden="true">
      <path d="M0 0 H222 C238 60 262 120 262 170 C262 230 248 280 242 309 H0 Z" fill="var(--orange)" transform="translate(8,0)"/>
      <path d="M0 0 H222 C238 60 262 120 262 170 C262 230 248 280 242 309 H0 Z" fill="var(--charcoal)"/>
    </svg>
    <div class="card__brand">
      <div class="brand">
        <span class="brand__dot"></span>
        <div>
          <div class="brand__name">K7 Services</div>
          <div class="brand__tagline">Clear Views From Above</div>
        </div>
      </div>
    </div>
    <div class="details">
      <h1 class="details__name">Marcus D. Hollin, MBA</h1>
      <p class="details__title">Director of Operations</p>
      <p class="details__address">1420 Ridgeway Road, Suite<br>210-118 Alpharetta, Georgia, 30005</p>
      <ul class="contact">
        <li><svg viewBox="0 0 24 24"><path d="M6.6 10.8a15 15 0 0 0 6.6 6.6l2.2-2.2a1 1 0 0 1 1-.25 11.4 11.4 0 0 0 3.6.57 1 1 0 0 1 1 1V20a1 1 0 0 1-1 1A17 17 0 0 1 3 4a1 1 0 0 1 1-1h3.5a1 1 0 0 1 1 1c0 1.25.2 2.45.57 3.6a1 1 0 0 1-.25 1z"/></svg>(555) 014 - 2290</li>
        <li><svg viewBox="0 0 24 24"><path d="M6 2h10v6H6zM4 9h16a2 2 0 0 1 2 2v7h-4v4H6v-4H2v-7a2 2 0 0 1 2-2zm4 8v3h8v-3z"/></svg>(555) 017 - 4418</li>
        <li><svg viewBox="0 0 24 24"><circle cx="12" cy="12" r="10"/></svg>www.kq7services.example</li>
      </ul>
      <p class="services">DRONE<span class="services__sep">|</span>WEBCAM<span class="services__sep">|</span>VIDEO</p>
    </div>
  </section>
</main>
</body>
</html>
```